organic, healthy living website needs a new home page!

We need a home page for the front page of our website (www.copperfernhollow.com.au).

We want to see the following at a glance! We want to gain trust - communicate value, and navigate visitors to the next step - purchasing!

Our two main products:
- certified organic veggies (weekly in Melbourne, Australia - Mentone, Frankston and Ringwood with more pick up locations to come soon)

-ethical wooden toys (by membership only at this stage - run quarterly as a bulk buy - just for Melbourne people!)

Other products:
- health appliances - juicers, dehydrators and water filters (free delivery to their door all over Australia)

- natural parenting products which promote breastfeeding, homebirth, cosleeping and gentle parenting (books, jewellery, gifts, blessingway etc) all over Australia - send via Bluegum Parcels.

This website holds all of our products for purchase. We want to emphasise exactly what is to offer here. We will have an info blog which we want to link THROUGH the product homepage of CF. The blog will include a directory of natural services (for a very niche market), recipes, stories, and a wealth of information to do with natural pregnancy, health, parenting, health and community!

We have 5 images linked below - we need these to correspond with the words PREGNANCY, BIRTH, PARENTING, HEALTH, And COMMUNITY and maybe a little design on these - such as dragonflies or flowers - or both. We will code these to work in a slideshow, and link to our blog.

We want this page to feature everything we do, but also be aesthetically pleasing without overkill. We want it to reflect our style, and vision. Natural, organic, and as close to nature as possible. Flow is important, as is consistency throughout the page. WE want it to appeal to our hippy mamas and papas who just want to love their babies, live organically and as healthy as they can.

We love the look and feel of the following websites:

http://thebrightlarderkit.com/

Thank you!!

Target Market(s)

20-50 year old parents who are environmentally aware and health conscious. They have very close bonds to their children.
Think bohemian, rustic, vintage yet with a modern feel.

Industry/Entity Type

Health

Font styles to use
Script

Colors
e34197
6b449b
33a6d7
0455a3
33b7a4

Requirements
Must have
• Must be clean and say at a glance exactly what we do.

```html
<!DOCTYPE html>
<html lang="en">
<head>
<meta charset="utf-8">
<title>Copperfern Hollow – Home</title>
<link href="https://fonts.googleapis.com/css2?family=Cinzel:wght@400;700&family=Open+Sans:wght@400;600;700&display=swap" rel="stylesheet">
<style>
:root{
  --pink:#e34197;
  --purple:#6b449b;
  --sky:#33a6d7;
  --navy:#0455a3;
  --teal:#33b7a4;
  --ink:#333;
  --muted:#777;
  --line:#d6d6d6;
  --paper:#f4f4f4;
  --search:#5c2d8f;
}
*{box-sizing:border-box;margin:0;padding:0}
html,body{width:1200px;height:2885px;overflow:hidden}
body{position:relative;background:#fff;font-family:"Open Sans",Arial,sans-serif;color:var(--ink)}
.abs{position:absolute}
a{color:inherit;text-decoration:none}

/* header */
.topbar{top:8px;right:32px;font-size:17px;color:#444}
.topbar svg{vertical-align:-3px;margin-right:6px}
.brand{left:30px;top:60px;display:flex;align-items:center;gap:18px}
.brand-dot{width:62px;height:62px;border-radius:50%;background:var(--purple)}
.brand-name{font-family:"Cinzel",Georgia,serif;font-size:40px;color:var(--purple);font-weight:700}
.search{left:600px;top:90px;width:440px;height:42px;border:1px solid #ccc;background:#fff;font-size:15px;padding:10px 14px;color:#555}
.search-btn{left:1046px;top:90px;width:122px;height:42px;background:var(--search);color:#fff;font-family:"Cinzel",serif;font-weight:700;font-size:18px;text-align:center;line-height:42px}
.cart{right:30px;top:146px;font-size:16px;color:#555}
.cart b{font-family:"Cinzel",serif;color:var(--purple);font-size:20px;margin-right:12px}

/* nav & hero */
.mainnav{left:22px;top:192px;width:336px;height:520px;border:1px solid var(--line);border-right:0;padding:10px 0 0 22px}
.mainnav li{list-style:none;border-bottom:1px solid var(--line);width:290px;height:68px;line-height:68px;font-family:"Cinzel",serif;font-size:19px;color:#222}
.mainnav li:last-child{border:0}
.hero{left:358px;top:192px;width:826px;height:520px;background:linear-gradient(135deg,#cfc5bb 0%,#b08a62 55%,#6b4e36 100%)}
.member-badge{left:1070px;top:404px;width:96px;height:96px;border-radius:50%;background:#fff;border:3px solid var(--teal)}
.hero-band{top:712px;height:74px;color:#fff;text-align:center}
.hero-band h2{font-family:"Cinzel",serif;font-size:28px;padding-top:8px;font-weight:700}
.hero-band p{font-size:14px;font-weight:600}
.band-toys{left:358px;width:413px;background:var(--pink)}
.band-veg{left:771px;width:413px;background:var(--teal)}

/* tabs & products */
.tabs{left:22px;top:822px;width:1156px;height:40px;border-bottom:1px solid var(--line);display:flex}
.tab{font-family:"Cinzel",serif;font-size:18px;color:var(--navy);padding:8px 18px;border:1px solid var(--line);border-bottom:0;margin-right:6px}
.tab.active{border-top:3px solid var(--sky)}
.product{top:895px;width:240px;text-align:center}
.product-img{height:210px;margin:0 auto;width:210px}
.product h3{font-size:16px;font-weight:400;margin-top:28px;border-top:1px dashed var(--line);padding-top:10px}
.product .price{font-size:16px;margin-top:4px}
.product .add{display:inline-block;margin-top:12px;background:var(--teal);color:#fff;font-size:11px;font-weight:700;padding:5px 18px;border-radius:3px}
.arrow{top:985px}

/* info panels */
.info{top:1252px;width:578px;height:280px;border:1px solid var(--line);padding:16px 18px}
.info h2{font-family:"Cinzel",serif;color:var(--navy);font-size:32px}
.info ul{list-style:none;font-size:16px;line-height:23px;margin-top:10px;width:260px}
.info-photo{top:46px;right:10px;width:270px;height:224px}
.social-btn{position:absolute;left:18px;bottom:14px;background:var(--navy);color:#fff;font-size:14px;padding:8px 16px}

/* promo boxes */
.promo{top:1572px;width:370px;height:194px;color:#fff;text-align:center;padding:18px}
.promo h2{font-family:"Cinzel",serif;font-size:30px;line-height:36px;font-weight:700}
.promo-refer{left:22px;background:var(--teal)}
.promo-news{left:415px;background:var(--pink)}
.promo-love{left:806px;background:var(--purple);text-align:left}
.promo-love h2{text-align:center}
.news-field{display:flex;margin:16px auto 0;width:330px;height:44px}
.news-field span{flex:1;background:#fff;color:#555;font-size:16px;text-align:left;padding:11px 12px}
.news-field b{width:110px;background:var(--purple);line-height:44px;font-family:"Cinzel",serif;font-size:20px}
.promo-news small{display:block;font-family:"Cinzel",serif;font-size:15px;margin-top:12px;font-weight:700}
.quote{font-size:15px;line-height:20px;margin-top:8px;font-weight:600}
.quote-by{text-align:right;font-style:italic;font-size:14px;margin-top:6px}

/* blog */
.blog-title{top:1800px;left:0;width:1200px;text-align:center}
.blog-title h2{display:inline-block;background:#fff;padding:0 16px;font-family:"Cinzel",serif;color:var(--navy);font-size:32px;position:relative}
.blog-title:before{content:"";position:absolute;left:18px;right:18px;top:22px;border-top:3px dotted var(--sky)}
.blog-card{top:1855px;width:226px;height:330px}
.blog-card .ribbon{height:50px;color:#fff;font-family:"Cinzel",serif;font-weight:700;font-size:22px;padding:10px 14px}
.blog-card .photo{height:232px}
.blog-card .more{display:block;color:var(--navy);font-size:15px;padding:14px 16px;border-bottom:1px solid var(--line)}

/* footer */
.footer-links{top:2238px;left:0;width:1200px;height:200px;background:var(--paper)}
.fcol{position:absolute;top:14px;font-size:15px;line-height:23px}
.fcol h4{font-family:"Cinzel",serif;font-size:16px;margin-bottom:4px}
.help{top:2440px;left:0;width:1200px;height:64px;background:var(--paper);border-top:1px solid var(--line)}
.help p{position:absolute;left:18px;top:18px;font-family:"Cinzel",serif;font-size:20px;font-weight:700}
.help .become{position:absolute;right:30px;top:10px;width:276px;height:44px;background:var(--purple);color:#fff;font-family:"Cinzel",serif;font-size:22px;text-align:center;line-height:44px}
.bottom{top:2504px;left:0;width:1200px;height:306px;background:var(--paper)}
.stats{position:absolute;left:14px;top:36px;width:400px;font-family:"Cinzel",serif;font-size:26px;line-height:37px;white-space:nowrap}
.stats strong{display:block;font-size:44px;letter-spacing:5px;margin-top:8px;line-height:48px}
.seal{position:absolute;top:42px;width:176px;height:176px;border-radius:50%}
.pay{position:absolute;left:872px;top:36px;font-family:"Cinzel",serif}
.pay h4{font-size:30px;font-weight:400}
.pay-row{display:flex;align-items:center;gap:14px;font-family:"Open Sans",sans-serif;font-size:16px;margin-top:18px}
.pay-row i{display:block;width:100px;height:36px;background:#dde3ec}
.copyright{top:2810px;left:0;width:1200px;height:75px;background:#e9e9e9;border-top:1px solid #ccc;text-align:center;font-size:16px;line-height:75px}
</style>
</head>
<body>

<header>
  <div class="abs topbar">
    <svg width="16" height="16" viewBox="0 0 24 24"><path fill="#33a6d7" d="M6.6 10.8a15.1 15.1 0 006.6 6.6l2.2-2.2c.3-.3.7-.4 1-.2 1.1.4 2.3.6 3.6.6.6 0 1 .4 1 1V20c0 .6-.4 1-1 1A17 17 0 013 4c0-.6.4-1 1-1h3.5c.6 0 1 .4 1 1 0 1.3.2 2.5.6 3.6.1.3 0 .7-.2 1z"/></svg>123-555-0147 | My account | Track order | Log in
  </div>
  <div class="abs brand"><span class="brand-dot"></span><span class="brand-name">Copperfern Hollow</span></div>
  <div class="abs search">Enter product name or code</div>
  <div class="abs search-btn">Search</div>
  <div class="abs cart"><b>My Cart</b>2 Items - $40.00</div>
</header>

<nav class="abs mainnav">
  <ul>
    <li>Home</li><li>Certified Organic Produce</li><li>Ethical Wooden Toys</li><li>Health Promotion</li><li>Natural Parenting</li><li>Register</li><li>Contact Us</li>
  </ul>
</nav>
<div class="abs hero" role="img" aria-label="Child's hand pushing a wooden toy car across a table"></div>
<div class="abs member-badge" role="img" aria-label="Melbourne members badge"></div>
<div class="abs hero-band band-toys"><h2>Ethical Wooden Toys</h2><p>Members Only</p></div>
<div class="abs hero-band band-veg"><h2>Veggies &amp; Fruits</h2><p>Open To Everyone</p></div>

<section>
  <div class="abs tabs">
    <span class="tab active">Parenting Products</span><span class="tab">Health Appliances</span><span class="tab">Toys</span>
  </div>
  <svg class="abs arrow" style="left:34px" width="20" height="34" viewBox="0 0 20 34"><path d="M17 3L4 17l13 14" stroke="#888" stroke-width="4" fill="none"/></svg>
  <svg class="abs arrow" style="left:1146px" width="20" height="34" viewBox="0 0 20 34"><path d="M3 3l13 14L3 31" stroke="#888" stroke-width="4" fill="none"/></svg>
  <div class="abs product" style="left:80px"><div class="product-img" role="img" aria-label="Red mommy bag with baby goods" style="background:linear-gradient(#d3303a,#8e1a22)"></div><h3>My First Mommy Bag</h3><p class="price">$49.00</p><span class="add">ADD TO CART</span></div>
  <div class="abs product" style="left:350px"><div class="product-img" role="img" aria-label="Pack of size medium diapers" style="background:linear-gradient(#3fa34d,#1e6fb5)"></div><h3>Softnest Medium Size Diapers</h3><p class="price">$15.00</p><span class="add">ADD TO CART</span></div>
  <div class="abs product" style="left:620px"><div class="product-img" role="img" aria-label="Herbal baby soap bar and box" style="background:linear-gradient(#f4f0e6,#c9d8a8)"></div><h3>Meadowleaf Herbals Baby Soap</h3><p class="price">$10.00</p><span class="add">ADD TO CART</span></div>
  <div class="abs product" style="left:890px"><div class="product-img" role="img" aria-label="Colourful baby activity gym" style="background:linear-gradient(#f0c23a,#3a9ad9)"></div><h3>Sunny Sprout Zoo Activity Gym</h3><p class="price">$70.00</p><span class="add">ADD TO CART</span></div>
</section>

<section>
  <div class="abs info" style="left:18px">
    <h2>Copperfern Hollow</h2>
    <ul><li>Baby Goods/Kids Goods</li><li>Natural pregnancy, birth and parenting support, information and products!</li><li>ORDERS: hello@copperfernhollow.com.au</li></ul>
    <div class="abs info-photo" role="img" aria-label="Pregnant woman with a basket of fresh vegetables" style="background:linear-gradient(135deg,#eee9e2,#8fb870)"></div>
    <span class="social-btn">Like Our Friendbook Page</span>
  </div>
  <div class="abs info" style="left:606px">
    <h2>Copperfern Hollow</h2>
    <ul><li>Health Food Store</li><li>Fruit &amp; Vegetable Store</li><li>Toy Store</li><li>&bull; Always Open</li></ul>
    <div class="abs info-photo" role="img" aria-label="Smiling baby lying on a soft blanket, Melbourne members" style="background:linear-gradient(135deg,#f1f1f1,#d9c6b5)"></div>
    <span class="social-btn">Like Our Friendbook Page</span>
  </div>
</section>

<section>
  <div class="abs promo promo-refer"><h2 style="margin-top:16px">Refer your friend &amp; get 10% off on your purchase</h2></div>
  <div class="abs promo promo-news"><h2>Join Free Newsletter</h2><div class="news-field"><span>Enter Email</span><b>Join</b></div><small>For Special Offers &amp; Promotions</small></div>
  <div class="abs promo promo-love"><h2>They Loved Us</h2><p class="quote">“Copperfern Produce is the best and most economical that I have found to buy from. The quality and freshness is great. Good variety and seasonal produce.”</p><p class="quote-by">Maya Lindqvist (Friendbook)</p></div>
</section>

<section>
  <div class="abs blog-title"><h2>Our Blog Posts</h2></div>
  <div class="abs blog-card" style="left:18px"><div class="ribbon" style="background:var(--purple)">Pregnancy</div><div class="photo" role="img" aria-label="Pregnant belly with a pendant necklace" style="background:linear-gradient(#e6c7a8,#b37a52)"></div><a class="more">Read now →</a></div>
  <div class="abs blog-card" style="left:250px"><div class="ribbon" style="background:var(--pink)">Birth</div><div class="photo" role="img" aria-label="Black and white photo of a mother at birth" style="background:linear-gradient(#d9d9d9,#6d6d6d)"></div><a class="more">Read now →</a></div>
  <div class="abs blog-card" style="left:482px"><div class="ribbon" style="background:var(--sky)">Parenting</div><div class="photo" role="img" aria-label="Family walking on a beach at sunset" style="background:linear-gradient(#f2d9a8,#c9a070)"></div><a class="more">Read now →</a></div>
  <div class="abs blog-card" style="left:714px"><div class="ribbon" style="background:var(--teal)">Health</div><div class="photo" role="img" aria-label="Basket of fresh fruit and vegetables" style="background:linear-gradient(#e7b35a,#a2402c)"></div><a class="more">Read now →</a></div>
  <div class="abs blog-card" style="left:946px"><div class="ribbon" style="background:var(--navy)">Community</div><div class="photo" role="img" aria-label="Many hands arranged in a circle" style="background:linear-gradient(#ece3d8,#c49a7a)"></div><a class="more">Read now →</a></div>
</section>

<footer>
  <div class="abs footer-links">
    <div class="fcol" style="left:18px"><h4>Copperfern Hollow</h4><p>About Company</p><p>Privacy Policy</p><p>Why Us</p><p>Shipping Policy</p><p>Returns &amp; Exchange</p></div>
    <div class="fcol" style="left:256px"><h4>Account</h4><p>Create Account</p><p>Manage Account</p><p>Change Password</p><p>Coupons &amp; Offers</p><p>My Shopping Bag</p></div>
    <div class="fcol" style="left:496px"><h4>Shop</h4><p>Wooden Toys</p><p>Organic Veggies</p><p>Organic Fruits</p><p>Parenting</p><p>Health Appliances</p></div>
    <div class="fcol" style="left:716px"><h4>Customer Care</h4><p>123-555-0147</p><p>Track Your Order</p><p>Email Us</p><p>Join Newsletter</p><p>Ask Our Expert</p></div>
    <div class="fcol" style="left:932px"><h4>Connect Social</h4><p>Friendbook · Circlenet</p><p>Chirper · Pinboard</p><p>Snapwall</p></div>
  </div>
  <div class="abs help"><p>Need help? Contact Us / (Or) Call Us : 123-555-0199</p><span class="become">Become Member</span></div>
  <div class="abs bottom">
    <div class="stats">100+ Oraganic<br>2000+ Toys<br>100+ Natural Parenting<br>100+ Healthy Living<strong>Products</strong></div>
    <div class="seal" style="left:430px;background:var(--teal)" role="img" aria-label="Fresh seal"></div>
    <div class="seal" style="left:640px;background:#1f6b3a" role="img" aria-label="Organic certificate seal"></div>
    <div class="pay"><h4>Payment Accepted</h4>
      <div class="pay-row"><i></i>Bank Deposit</div>
      <div class="pay-row"><i></i>PayWell</div>
    </div>
  </div>
  <div class="abs copyright">© 2004-2014 Copperfern Hollow. All Rights Reserved. / Terms &amp; Conditions | Read Our Privacy Policy</div>
</footer>

</body>
</html>
```